Corvane Capital Business Cards

These are professional business cards that are for my family office.
Put fake emails and phone numbers as of now until I finalize those components. This family office controls my families investments, assets, and future. The cards should be professional.
..
.
.
.
I just uploaded another variation of a logo I would like to see as a business card to I am inbeteen which logo to use

Target Market(s)

business

Industry/Entity Type

business

Contact Information for Business Card

Professional, wealth related, finance related.

Requirements
Must have
• Logo

```html
<!DOCTYPE html>
<html lang="en">
<head>
<meta charset="utf-8">
<title>Corvane Capital Business Cards</title>
<link href="https://fonts.googleapis.com/css2?family=Bodoni+Moda:wght@500&family=Poppins:wght@400&display=swap" rel="stylesheet">
<style>
  :root {
    --backdrop: #c9c9c9;
    --gold: #c8b073;
    --gold-deep: #b59f69;
    --gold-light: #d4c08a;
    --ink: #111111;
    --paper: #ffffff;
    --mist: #ececec;
    --text: #222222;
  }
  * { margin: 0; padding: 0; box-sizing: border-box; }
  html, body { width: 1200px; height: 900px; overflow: hidden; background: var(--backdrop); }
  .canvas { position: relative; width: 1200px; height: 900px; }

  .card {
    position: absolute; left: 250px; width: 700px; height: 400px;
    border-radius: 28px; overflow: hidden;
    box-shadow: 0 6px 18px rgba(0,0,0,0.18);
  }

  /* Front */
  .card-front {
    top: 40px;
    background: linear-gradient(115deg, var(--gold) 0%, var(--gold-light) 40%, var(--gold-deep) 70%, var(--gold) 100%);
  }
  .front-band {
    position: absolute; inset: 0;
    background: linear-gradient(160deg, transparent 45%, rgba(150,130,80,0.18) 46%, rgba(150,130,80,0.18) 62%, transparent 63%);
  }
  .front-brand {
    position: absolute; left: 0; right: 0; top: 150px;
    display: flex; flex-direction: column; align-items: center; gap: 22px;
  }
  .brand-mark { width: 26px; height: 26px; background: var(--paper); }
  .front-brand .brand-name {
    font-family: "Bodoni Moda", serif; font-weight: 500;
    font-size: 46px; letter-spacing: 6px; color: var(--paper);
  }

  /* Back */
  .card-back {
    top: 470px; background: var(--paper);
  }
  .back-band {
    position: absolute; inset: 0;
    background: linear-gradient(155deg, transparent 38%, var(--mist) 39%, #f6f6f6 58%, transparent 59%);
  }
  .back-tab {
    position: absolute; right: 0; top: 44px; width: 12px; height: 34px; background: var(--ink);
  }
  .back-brand {
    position: absolute; left: 50px; top: 120px;
    display: flex; align-items: center; gap: 16px;
  }
  .back-brand .brand-mark { background: var(--gold); width: 20px; height: 20px; }
  .back-brand .brand-name {
    font-family: "Bodoni Moda", serif; font-weight: 500;
    font-size: 38px; letter-spacing: 4px; color: var(--ink);
  }

  .holder { position: absolute; right: 60px; top: 48px; text-align: right; }
  .holder-name {
    font-family: "Bodoni Moda", serif; font-weight: 500;
    font-size: 24px; letter-spacing: 2px; color: var(--ink);
  }
  .holder-name .surname { color: var(--gold); }
  .holder-title {
    font-family: "Poppins", sans-serif; font-size: 17px; color: var(--text); margin-top: 2px;
  }

  .contact-list {
    position: absolute; left: 50px; bottom: 44px; list-style: none;
    font-family: "Poppins", sans-serif; font-size: 18px; color: var(--text);
  }
  .contact-list li { display: flex; align-items: center; gap: 12px; line-height: 30px; }
  .contact-list svg { width: 18px; height: 18px; fill: none; stroke: var(--gold); stroke-width: 2; }

  .address {
    position: absolute; right: 60px; bottom: 60px; text-align: right;
    font-family: "Poppins", sans-serif; font-size: 18px; line-height: 28px; color: var(--text);
  }
</style>
</head>
<body>
<main class="canvas">
  <section class="card card-front">
    <div class="front-band"></div>
    <div class="front-brand">
      <span class="brand-mark"></span>
      <span class="brand-name">CORVANE CAPITAL</span>
    </div>
  </section>

  <section class="card card-back">
    <div class="back-band"></div>
    <span class="back-tab"></span>

    <div class="holder">
      <p class="holder-name">ELIAS <span class="surname">MARROW</span></p>
      <p class="holder-title">Managing Director</p>
    </div>

    <div class="back-brand">
      <span class="brand-mark"></span>
      <span class="brand-name">CORVANE CAPITAL</span>
    </div>

    <ul class="contact-list">
      <li>
        <svg viewBox="0 0 24 24"><path d="M5 3h4l2 5-3 2a12 12 0 0 0 6 6l2-3 5 2v4a2 2 0 0 1-2 2A17 17 0 0 1 3 5a2 2 0 0 1 2-2z"/></svg>
        044-555 010 202
      </li>
      <li>
        <svg viewBox="0 0 24 24"><rect x="3" y="5" width="18" height="14"/><path d="M3 5l9 8 9-8"/></svg>
        info@corvanemail.com
      </li>
      <li>
        <svg viewBox="0 0 24 24"><circle cx="12" cy="12" r="9"/><path d="M3 12h18M12 3c3 3 3 15 0 18M12 3c-3 3-3 15 0 18"/></svg>
        www.corvanecapital.com
      </li>
    </ul>

    <p class="address">18 Harrowgate Lane, Suite 4<br>60231, Northvale</p>
  </section>
</main>
</body>
</html>
```